Modern Business Card

Modern professional business card with more than just logo and demographic info. Something memorable.

We are a trendy/modern chiropractic group with an emphasis on neurology, hence the minimalist-type brain logo. We want to convey that modern and technical aspect with professionalism and the elite nature of our practice environment.

```html
<!DOCTYPE html>
<html lang="en">
<head>
<meta charset="utf-8">
<title>Keystone Spine – Business Card</title>
<link rel="stylesheet" href="https://fonts.googleapis.com/css2?family=Quattrocento:wght@400;700&family=Signika:wght@600&family=Roboto:wght@400&display=swap">
<style>
  :root {
    --bg: #b9b9b9;
    --card: #f1f1f1;
    --ink: #1d1a1c;
    --text: #3a3438;
    --blue: #3a5f9c;
    --brown: #433538;
    --faint: #e2e4e8;
  }
  * { margin: 0; padding: 0; box-sizing: border-box; }
  html, body { width: 1200px; height: 576px; overflow: hidden; background: var(--bg); }
  .canvas { position: relative; width: 1200px; height: 576px; }
  .card {
    position: absolute; top: 138px; width: 484px; height: 294px;
    background: var(--card); border-radius: 10px; overflow: hidden;
    font-family: "Quattrocento", Georgia, serif; color: var(--text);
  }
  .card--front { left: 82px; }
  .card--back { left: 602px; }

  .brand { position: absolute; display: flex; align-items: center; }
  .brand__mark { background: var(--blue); flex: none; }
  .brand__name {
    font-family: "Quattrocento", Georgia, serif; font-weight: 400;
    color: var(--ink); text-transform: uppercase; line-height: 1;
  }
  .card--front .brand { left: 92px; top: 106px; gap: 18px; }
  .card--front .brand__mark { width: 26px; height: 26px; }
  .card--front .brand__name { font-size: 42px; letter-spacing: 1px; }
  .card--back .brand { left: 28px; top: 44px; gap: 14px; }
  .card--back .brand__mark { width: 20px; height: 20px; }
  .card--back .brand__name { font-size: 32px; letter-spacing: 1px; }

  .front__web {
    position: absolute; left: 0; right: 0; top: 246px;
    display: flex; justify-content: center; align-items: center; gap: 24px;
    font-family: "Roboto", Arial, sans-serif; font-size: 12.5px; color: var(--ink);
  }
  .front__dash { width: 34px; height: 2px; background: var(--blue); border-radius: 2px; }
  .front__bar { position: absolute; left: 0; right: 0; bottom: 0; height: 13px; display: flex; }
  .front__bar span { flex: 1; }
  .front__bar .bar-blue { background: var(--blue); }
  .front__bar .bar-brown { background: var(--brown); }

  .back__accent {
    position: absolute; right: 14px; top: 20px; width: 180px; height: 200px;
    background: var(--faint); border-radius: 18px; opacity: .7;
  }
  .person { position: absolute; left: 28px; top: 161px; }
  .person__name { font-family: "Signika", Arial, sans-serif; font-weight: 600; font-size: 18px; color: var(--blue); }
  .person__role { font-size: 13px; margin-top: 2px; }
  .address { position: absolute; left: 28px; top: 228px; font-size: 13px; line-height: 18px; }
  .contact { position: absolute; left: 258px; top: 162px; list-style: none; font-size: 12.5px; }
  .contact li { display: flex; align-items: center; gap: 9px; height: 18px; }
  .contact svg { width: 11px; height: 11px; fill: var(--blue); flex: none; }
  .back__strip { position: absolute; left: 0; bottom: 0; width: 260px; height: 11px; background: var(--brown); }
  .back__tab {
    position: absolute; right: 0; bottom: 0; width: 292px; height: 36px;
    background: var(--blue); clip-path: polygon(6% 0, 100% 0, 100% 100%, 0 100%);
    color: #e8ecf4; font-size: 13px; display: flex; align-items: center; justify-content: center;
  }
</style>
</head>
<body>
<main class="canvas">
  <section class="card card--front">
    <div class="brand">
      <span class="brand__mark"></span>
      <span class="brand__name">Keystone<br>Spine</span>
    </div>
    <p class="front__web"><span class="front__dash"></span>www.keystonespine.com<span class="front__dash"></span></p>
    <div class="front__bar"><span class="bar-blue"></span><span class="bar-brown"></span></div>
  </section>

  <section class="card card--back">
    <div class="back__accent"></div>
    <div class="brand">
      <span class="brand__mark"></span>
      <span class="brand__name">Keystone<br>Spine</span>
    </div>
    <div class="person">
      <p class="person__name">Daniel Reyes Moore</p>
      <p class="person__role">Managing Director</p>
    </div>
    <p class="address">87 Harbor Lane, Millbrook,<br>Fairview, US 204518</p>
    <ul class="contact">
      <li><svg viewBox="0 0 12 12"><path d="M1 3.5C1 2 2.5 1 6 1s5 1 5 2.5V5H8.5V4h-5v1H1zM3 6h6l1.5 5h-9z"/></svg>555-014-2288</li>
      <li><svg viewBox="0 0 12 12"><path d="M0 2h12v8H0zM1 3v.5l5 3.5 5-3.5V3z"/></svg>daniel@keystonespine.com</li>
      <li><svg viewBox="0 0 12 12"><path d="M6 0a6 6 0 1 0 0 12A6 6 0 0 0 6 0zm0 1.2c.6.6 1.2 2 1.3 4H4.7c.1-2 .7-3.4 1.3-4zM1.3 5.2a4.8 4.8 0 0 1 2.4-3.5c-.5 1-.8 2.1-.9 3.5zm7.9 0c-.1-1.4-.4-2.5-.9-3.5a4.8 4.8 0 0 1 2.4 3.5zM1.3 6.8h1.5c.1 1.4.4 2.5.9 3.5a4.8 4.8 0 0 1-2.4-3.5zm3.4 0h2.6c-.1 2-.7 3.4-1.3 4-.6-.6-1.2-2-1.3-4zm4.5 0h1.5a4.8 4.8 0 0 1-2.4 3.5c.5-1 .8-2.1.9-3.5z"/></svg>www.keystonespine.com</li>
    </ul>
    <div class="back__strip"></div>
    <div class="back__tab">Keystone Spine LLC</div>
  </section>
</main>
</body>
</html>
```